Flat bootstrap design for existing site

I'm looking for a modern flat design based around an existing logo. This has to be a custom design (no external templates), and implemented into a bootstrap framework.

The logo is attached as 2 versions - choose whichever you want, that flows better with whatever design you choose.

Added screenshots of the existing site (currently using the default bootstrap layouts). Please make your designs around those pages in the screenshots (i.e. the homepage only has the postal code input and the header). The active page has 3 screenshots, because I wanted to illustrate the other states that would be visible (in the table rows).

This is a moving/junk removal website, just for some context.

Here's some example websites (flat designs) that I like, just to give you an idea of what I'm after.

https://www.plimvora.com/
https://dacklow.com/
https://trevanu.com/
https://quobrintal.com/en/

Coding

Coded - Design and coding required

Number of Pages Required

5+ page

Colors

Designer to choose colors to be used in the design.

Requirements
Must have
• It must be a modern/simple flat design, that is built around the existing logo (attached).
• It has to be implemented using bootstrap.

```html
<!DOCTYPE html>
<html lang="en">
<head>
<meta charset="utf-8">
<title>KARVEO – Junk Removal</title>
<link href="https://fonts.googleapis.com/css2?family=Open+Sans:wght@400;600;700&family=Raleway:wght@300&display=swap" rel="stylesheet">
<style>
  :root {
    --sky: #38bdf2;
    --band: #4f8fcf;
    --white: #ffffff;
    --purple: #6a5fad;
    --green: #8cc63f;
    --ink: #3d3a6b;
    --muted: #9a98a8;
    --figure-orange: #f39a2c;
    --figure-teal: #4fb7c6;
  }
  * { margin: 0; padding: 0; box-sizing: border-box; }
  html, body { width: 1200px; height: 621px; overflow: hidden; }
  body { font-family: "Open Sans", sans-serif; background: var(--white); position: relative; }

  .hero { position: absolute; left: 0; top: 0; width: 1200px; height: 556px; background: var(--sky); overflow: hidden; }
  .hero-shapes { position: absolute; inset: 0; }

  .site-header { position: absolute; left: 144px; right: 144px; top: 16px; height: 48px; display: flex; align-items: center; }
  .brand { display: flex; align-items: center; gap: 8px; color: var(--white); font-weight: 700; font-size: 32px; letter-spacing: 1px; text-decoration: none; }
  .brand-dot { width: 14px; height: 14px; border-radius: 50%; background: var(--white); }
  .main-nav { margin-left: auto; display: flex; align-items: center; }
  .nav-link { color: var(--white); text-decoration: none; font-weight: 600; font-size: 14px; margin-right: 27px; position: relative; }
  .nav-link.is-active::after { content: ""; position: absolute; left: 50%; bottom: -7px; width: 12px; height: 2px; margin-left: -6px; background: var(--white); }
  .signin { margin-left: 16px; margin-right: 0; background: var(--purple); color: var(--white); font-weight: 600; font-size: 14px; width: 81px; height: 34px; border-radius: 3px; display: flex; align-items: center; justify-content: center; text-decoration: none; }

  .headline { position: absolute; left: 242px; width: 500px; top: 166px; text-align: center; font-family: "Raleway", sans-serif; font-weight: 300; color: var(--white); font-size: 46px; line-height: 54px; }

  .booking { position: absolute; left: 352px; top: 294px; width: 285px; height: 50px; display: flex; box-shadow: 0 8px 18px rgba(30, 90, 140, 0.25); border-radius: 3px; overflow: hidden; }
  .postal-input { flex: 1; border: 0; padding-left: 16px; font-family: "Open Sans", sans-serif; font-size: 13px; color: var(--ink); background: var(--white); }
  .postal-input::placeholder { color: var(--muted); }
  .book-btn { width: 94px; border: 0; background: var(--green); color: var(--white); font-family: "Open Sans", sans-serif; font-weight: 700; font-size: 13px; display: flex; align-items: center; justify-content: center; gap: 8px; }

  .hero-figure { position: absolute; left: 808px; top: 100px; width: 280px; height: 312px; border-radius: 40px 40px 8px 8px; background: linear-gradient(180deg, var(--figure-orange) 0%, var(--figure-orange) 45%, var(--figure-teal) 46%, var(--figure-teal) 100%); opacity: 0.9; }

  .site-footer { position: absolute; left: 0; top: 556px; width: 1200px; height: 58px; display: flex; align-items: center; padding: 0 144px; }
  .copyright { color: var(--ink); font-size: 13px; }
  .social { margin-left: auto; display: flex; gap: 6px; }
  .social-square { width: 19px; height: 19px; border-radius: 2px; background: var(--purple); }
  .footer-bar { position: absolute; left: 0; bottom: 0; width: 1200px; height: 7px; background: var(--purple); }
</style>
</head>
<body>
  <section class="hero">
    <svg class="hero-shapes" width="1200" height="556" viewBox="0 0 1200 556">
      <path fill="var(--band)" d="M400 556 Q560 556 660 490 L1200 150 L1200 190 L700 556 Z"/>
      <path fill="var(--white)" d="M560 556 Q640 556 700 516 L1200 124 L1200 284 L1128 356 Q1100 384 1128 412 L1200 500 L1200 556 Z"/>
    </svg>

    <header class="site-header">
      <a class="brand" href="#"><span class="brand-dot"></span>KARVEO</a>
      <nav class="main-nav">
        <a class="nav-link" href="#">BOOK</a>
        <a class="nav-link" href="#">HOW IT WORKS</a>
        <a class="nav-link is-active" href="#">BECOME A DRIVER</a>
        <a class="signin" href="#">SIGNIN</a>
      </nav>
    </header>

    <h1 class="headline">Need junk removed?<br>Book now.</h1>

    <form class="booking">
      <input class="postal-input" type="text" placeholder="Postal Code">
      <button class="book-btn" type="button">BOOK
        <svg width="18" height="8" viewBox="0 0 18 8"><path d="M0 4 H16 M13 1 L16 4 L13 7" stroke="#fff" stroke-width="1.3" fill="none"/></svg>
      </button>
    </form>

    <div class="hero-figure" role="img" aria-label="Illustration of a smiling junk removal worker standing in a teal recycling bin with a broom and a rubbish bag"></div>
  </section>

  <footer class="site-footer">
    <p class="copyright">© 2017 KARVEO. All rights reserved.</p>
    <div class="social">
      <span class="social-square"></span>
      <span class="social-square"></span>
      <span class="social-square"></span>
    </div>
  </footer>
  <div class="footer-bar"></div>
</body>
</html>
```